We need a business card for our gym. We are a PowerCore affiliate in Decatur Georgie established 2008. Our company name is Rally Functional Fitness. PowerCore Building Prime Fitness. Instagram and website is @rallygym. Hashtags we use #rallywithheart #madetorally We want something similar to the the black and neon green design attached but a different color scheme. No neon colors. Are company colors are the same as the blue and white card attached. We are open to ideas as far as colors however - just no neon.

Contact Information for Business Card

Rally Functional Fitness
472 Halvern Drive
Decatur GA 30041
Phone 404.555.0187 Website www.rallygym.example

Font styles to use
Other font styles liked:
• Futura Extra Bold Condensed

Colors

Designer to choose colors to be used in the design.

Requirements
Must have
• Our primary font we typically use for our name is Futura Extra Bold Condensed
Nice to have
• I attached a card from that is black and neon green from Zorva that we would like something similar. The blue and white is more similar to our colors. We also use have used black and white in the past. We use the chevrons as out logo. We are a PowerCore affiliate so I included a logo from them as well that may or may not be used on the card. Our instagram is @rallygym hashtags #madetorally #rallywithheart
Should not have
• No neon colors

```html
<!DOCTYPE html>
<html lang="en">
<head>
<meta charset="utf-8">
<title>Rally Functional Fitness – Business Card</title>
<link rel="stylesheet" href="https://fonts.googleapis.com/css2?family=Bebas+Neue&family=Montserrat:wght@400;500;800&display=swap">
<style>
  :root {
    --backdrop: #2b2b2c;
    --card: #252526;
    --ink-dark: #0e0e0f;
    --sky: #8fd4f6;
    --sky-soft: #7cc6ea;
  }
  * { box-sizing: border-box; margin: 0; padding: 0; }
  html, body {
    width: 1200px; height: 901px; overflow: hidden;
    background: var(--backdrop);
  }
  .sheet {
    width: 1200px; height: 901px;
    display: flex; flex-direction: column; align-items: center; justify-content: center;
    gap: 40px;
  }
  .card {
    position: relative;
    width: 640px; height: 366px;
    background: var(--card);
    box-shadow: 0 10px 28px rgba(0,0,0,.45);
    overflow: hidden;
  }
  .card__band {
    position: absolute; left: 0; right: 0; bottom: 0;
    height: 9px; background: var(--sky);
  }

  /* Front */
  .brand {
    position: absolute; left: 0; right: 0; top: 108px;
    text-align: center;
    font-family: "Montserrat", sans-serif; font-weight: 800;
    color: var(--ink-dark);
    line-height: 1;
  }
  .brand__name { display: block; font-size: 92px; letter-spacing: -1px; }
  .brand__tag  { display: block; font-size: 30px; margin-top: 4px; letter-spacing: 0; }

  /* Back */
  .person {
    position: absolute; top: 118px; right: 352px;
    text-align: right;
  }
  .person__name {
    font-family: "Bebas Neue", sans-serif;
    font-size: 42px; color: var(--sky); letter-spacing: .5px; line-height: 1;
  }
  .person__role {
    font-family: "Montserrat", sans-serif; font-weight: 400;
    font-size: 17px; color: var(--sky-soft); letter-spacing: .8px; margin-top: 4px;
  }
  .divider {
    position: absolute; left: 306px; top: 122px;
    width: 1.5px; height: 76px; background: var(--sky-soft); opacity: .8;
  }
  .contact {
    position: absolute; left: 324px; top: 128px;
    list-style: none;
    font-family: "Montserrat", sans-serif; font-weight: 500;
    font-size: 17px; color: var(--sky); line-height: 24px;
  }
  .contact__item { display: flex; align-items: center; gap: 8px; }
  .contact__icon { width: 14px; height: 14px; fill: var(--sky); flex: none; }
  .address {
    position: absolute; left: 0; right: 0; bottom: 40px;
    text-align: center;
    font-family: "Montserrat", sans-serif; font-weight: 500;
    font-size: 18px; color: var(--sky); letter-spacing: .4px;
  }
</style>
</head>
<body>
<main class="sheet">
  <section class="card card--front" aria-label="Card front">
    <h1 class="brand">
      <span class="brand__name">RALLY</span>
      <span class="brand__tag">FUNCTIONAL FITNESS</span>
    </h1>
    <div class="card__band"></div>
  </section>

  <section class="card card--back" aria-label="Card back">
    <div class="person">
      <h2 class="person__name">MARCUS DELANEY</h2>
      <p class="person__role">EXPERT COACHES</p>
    </div>
    <div class="divider"></div>
    <ul class="contact">
      <li class="contact__item">
        <svg class="contact__icon" viewBox="0 0 16 16" aria-hidden="true"><path d="M3.6 1.2 6 3.6 4.7 5.6c.9 2.2 3.4 4.7 5.7 5.7l2-1.3 2.4 2.4-1.6 2.2C7.8 14.4 1.6 8.2 1.4 2.8z"/></svg>
        404.555.0187
      </li>
      <li class="contact__item">
        <svg class="contact__icon" viewBox="0 0 16 16" aria-hidden="true"><path d="M1 3h14v1.2L8 8.6 1 4.2zM1 5.6l7 4.4 7-4.4V13H1z"/></svg>
        info@rallygym.example
      </li>
      <li class="contact__item">
        <svg class="contact__icon" viewBox="0 0 16 16" aria-hidden="true"><path fill-rule="evenodd" d="M8 1a7 7 0 1 1 0 14A7 7 0 0 1 8 1zm0 1.6a5.4 5.4 0 1 0 0 10.8A5.4 5.4 0 0 0 8 2.6zM8 5a3 3 0 1 1 0 6 3 3 0 0 1 0-6z"/></svg>
        www.rallygym.example
      </li>
    </ul>
    <p class="address">472 Halvern Drive, Decatur GA 30041</p>
    <div class="card__band"></div>
  </section>
</main>
</body>
</html>
```